Looking for a modern, Professional business card design

We have a simple business card, but are looking for a more modern, professional look. A sample of the basic card is attached as well as the logo. We would also like to add that we offer:
Struggling with your finances?
- Learn to become debt free
- Discover the power of cash
- Control your money instead of it controlling you
Let us help you achieve a new level of financial freedom!
Also, we would like to have a "SPECIAL OFFER!: FREE 30 minute consultation"
Financial Planning

```html
<!DOCTYPE html>
<html lang="en">
<head>
<meta charset="utf-8">
<title>Liberty Money Coaching – Business Card</title>
<link rel="stylesheet" href="https://fonts.googleapis.com/css2?family=Arimo:wght@400;700&family=Roboto+Condensed:wght@700;800&display=swap">
<style>
  :root {
    --backdrop: #8e8f8e;
    --paper: #f1f1f1;
    --ink: #111111;
    --black: #050505;
    --green: #2a8c3f;
    --green-bright: #3aa14a;
    --green-light: #8cc63f;
    --green-text: #2f9a44;
    --white: #ffffff;
    --muted: #555555;
  }
  * { box-sizing: border-box; margin: 0; padding: 0; }
  html, body { width: 1105px; height: 1200px; overflow: hidden; }
  body {
    background: var(--backdrop);
    font-family: "Arimo", Arial, sans-serif;
    position: relative;
  }
  .card {
    position: absolute;
    left: 178px;
    width: 748px;
    height: 425px;
    overflow: hidden;
  }
  .card--front { top: 119px; background: var(--paper); }
  .card--back { top: 637px; background: var(--green); color: var(--white); }

  .front-wave { position: absolute; left: 0; top: 0; width: 748px; height: 425px; }

  .brand { position: absolute; left: 40px; top: 82px; display: flex; align-items: center; gap: 16px; }
  .brand__dot { width: 52px; height: 52px; border-radius: 50%; background: var(--green-bright); }
  .brand__name { font-weight: 700; font-size: 40px; color: var(--ink); letter-spacing: 0.5px; }
  .brand__tagline { position: absolute; left: 108px; top: 150px; font-size: 14px; color: var(--muted); }

  .contact { position: absolute; left: 38px; top: 303px; list-style: none; }
  .contact__item { display: flex; align-items: center; height: 29px; color: var(--white); font-size: 20px; }
  .contact__icon { width: 18px; height: 18px; margin-right: 14px; fill: var(--green-bright); }

  .person { position: absolute; right: 48px; top: 335px; text-align: right; }
  .person__name { font-size: 27px; font-weight: 700; color: var(--green-text); letter-spacing: 0.5px; }
  .person__role { font-size: 21px; color: var(--white); margin-top: 4px; }

  .back-mark { position: absolute; right: -60px; top: 20px; width: 300px; height: 300px; border-radius: 50%; background: var(--green-bright); }

  .pitch { position: absolute; left: 62px; top: 74px; }
  .pitch__title { font-size: 23px; font-weight: 700; letter-spacing: 0.3px; }
  .pitch__list { list-style: none; margin-top: 10px; }
  .pitch__list li { font-size: 20px; height: 31.5px; line-height: 31.5px; }
  .pitch__list li::before { content: "•"; margin-right: 14px; }
  .pitch__cta { font-family: "Roboto Condensed", Arial, sans-serif; font-weight: 700; font-size: 20px; margin-top: 14px; }

  .offer { position: absolute; left: 62px; top: 258px; font-family: "Roboto Condensed", Arial, sans-serif; }
  .offer__title { font-size: 58px; font-weight: 800; line-height: 1; letter-spacing: 0.5px; color: #eef3ee; }
  .offer__detail { font-size: 26px; font-weight: 800; letter-spacing: 0.8px; margin-top: 6px; color: #eef3ee; }
</style>
</head>
<body>
  <section class="card card--front">
    <svg class="front-wave" viewBox="0 0 748 425" aria-hidden="true">
      <path d="M0 212 C180 240 320 262 460 244 C580 228 660 206 748 200 L748 218 C660 224 580 246 460 262 C320 280 180 260 0 232 Z" fill="#3aa14a"/>
      <path d="M0 228 C180 256 320 276 460 260 C580 244 660 222 748 216 L748 425 L0 425 Z" fill="#050505"/>
    </svg>
    <div class="brand">
      <span class="brand__dot"></span>
      <span class="brand__name">LIBERTY MONEY COACHING</span>
    </div>
    <p class="brand__tagline">Achieve a new level of personal freedom</p>

    <ul class="contact">
      <li class="contact__item">
        <svg class="contact__icon" viewBox="0 0 18 18"><rect x="4" y="0" width="10" height="18" rx="2"/><rect x="6" y="2.5" width="6" height="11" fill="#050505"/></svg>
        (205) 555-0182
      </li>
      <li class="contact__item">
        <svg class="contact__icon" viewBox="0 0 18 18"><rect x="0" y="3" width="18" height="12" rx="1"/><path d="M0 4 L9 10 L18 4" stroke="#050505" stroke-width="1.5" fill="none"/></svg>
        daniel@steadyledgercoach.com
      </li>
      <li class="contact__item">
        <svg class="contact__icon" viewBox="0 0 18 18"><circle cx="9" cy="9" r="9"/><path d="M0 9 H18 M9 0 C4 5 4 13 9 18 M9 0 C14 5 14 13 9 18" stroke="#050505" stroke-width="1.2" fill="none"/></svg>
        www.steadyledgercoach.com
      </li>
    </ul>

    <div class="person">
      <p class="person__name">DANIEL R. CARTER</p>
      <p class="person__role">Personal Financial Coach</p>
    </div>
  </section>

  <section class="card card--back">
    <span class="back-mark" aria-hidden="true"></span>
    <div class="pitch">
      <h2 class="pitch__title">STRUGGLING WITH YOUR FINANCES?</h2>
      <ul class="pitch__list">
        <li>Learn to become debt free</li>
        <li>Discover the power of cash</li>
        <li>Control your money instead of it controlling you</li>
      </ul>
      <p class="pitch__cta">Let us help you achieve a new level of financial freedom!</p>
    </div>
    <div class="offer">
      <p class="offer__title">SPECIAL OFFER!</p>
      <p class="offer__detail">FREE 30 MINUTE CONSULTATION</p>
    </div>
  </section>
</body>
</html>
```